fernwick study hub community

The website presents a new interactive learning system where it provides not only the teaching material as the instructor friend who can both teach and learn, making friends and making money.
Make friends and get money.

```html
<!DOCTYPE html>
<html lang="en">
<head>
<meta charset="utf-8">
<title>Fernwick Study Hub Community</title>
<link href="https://fonts.googleapis.com/css2?family=Roboto:wght@300;400;500;700&display=swap" rel="stylesheet">
<style>
:root{
  --navy:#0b2036;
  --header:#0d3557;
  --cyan:#12a9e2;
  --cyan-dark:#0e8fc2;
  --hero-bg:#252628;
  --ink:#1b1b1b;
  --text:#444;
  --muted:#555;
  --grey-circle:#bdbdbd;
  --panel:#f0f0f0;
  --rule:#d6d6d6;
  --white:#fff;
}
*{box-sizing:border-box;margin:0;padding:0}
html,body{width:848px;height:1200px;overflow:hidden}
body{position:relative;background:var(--white);font-family:'Roboto',sans-serif;color:var(--text)}
.abs{position:absolute}

/* header */
.site-header{left:0;top:0;width:848px;height:48px;background:linear-gradient(180deg,#0a2a47,var(--header) 60%,#0b2c4a)}
.brand{left:62px;top:8px;display:flex;align-items:center;gap:8px;color:var(--white);font-weight:500;font-size:15px;letter-spacing:.5px}
.brand-dot{width:12px;height:12px;border-radius:50%;background:var(--cyan)}
.main-nav{left:0;top:48px;width:848px;height:32px;background:var(--cyan);display:flex}
.main-nav a{display:flex;align-items:center;height:32px;color:var(--white);text-decoration:none;font-size:9px;font-weight:500;text-transform:uppercase;border-right:1px solid rgba(255,255,255,.85)}
.main-nav a:last-child{border-right:none}

/* hero */
.hero{left:0;top:80px;width:848px;height:356px;background:var(--hero-bg)}
.hero-frame{left:72px;top:10px;width:704px;height:330px;border:1px solid #3a3b3d}
.hero-slide{left:79px;top:17px;width:690px;height:317px;background:linear-gradient(100deg,#d9dde3 0%,#f2f3f5 35%,#eef5f4 60%,#9fd7cd 85%,#d8efea 100%)}
.hero-caption{left:490px;top:181px;font-size:17px;font-weight:300;line-height:25.5px;color:#333;text-transform:uppercase}
.slide-arrow{top:158px;width:34px;height:34px;background:#0a0a0a;display:flex;align-items:center;justify-content:center}

/* intro */
.intro{left:73px;top:436px;width:704px;height:342px;border-left:1px solid var(--rule);border-right:1px solid var(--rule)}
.intro-title{left:0;top:16px;width:704px;text-align:center;font-size:22px;font-weight:300;color:var(--ink)}
.intro-text{left:45px;top:45px;width:614px;text-align:center;font-size:10.5px;font-weight:300;line-height:16px;color:#333}
.bubble{border-radius:50%;background:var(--grey-circle);display:flex;align-items:center;justify-content:center;text-align:center;font-size:17px;font-weight:300;line-height:23px;color:#222}
.bubble-shadow{height:8px;border-radius:50%;background:radial-gradient(ellipse at center,rgba(0,0,0,.12),rgba(0,0,0,0) 70%)}
.rule{left:0;width:848px;height:1px;background:var(--rule)}

/* news */
.news-panel{left:75px;top:784px;width:699px;height:230px;background:var(--panel)}
.news-heading{left:90px;top:796px;font-size:21px;color:var(--ink);font-weight:300}
.news-heading b{font-weight:700}
.news-item{display:flex;gap:6px;width:200px}
.chev{flex:none;width:18px;height:18px;border-radius:50%;background:var(--cyan);display:flex;align-items:center;justify-content:center;margin-top:2px}
.news-item h3{font-size:11.5px;font-weight:400;color:var(--cyan);line-height:14px}
.news-item p{font-size:9px;line-height:12px;color:#333;margin-top:2px}
.about-card{left:510px;top:794px;width:252px;height:202px;background:var(--white)}
.about-card h2{position:absolute;left:13px;top:9px;font-size:19.5px;font-weight:300;color:var(--ink)}
.about-card h2 b{font-weight:700}
.about-photo{left:0;top:38px;width:252px;height:164px;background:linear-gradient(180deg,#e7edf3 0%,#cfd8e2 40%,#48505c 75%,#2b2f37 100%)}
.about-caption{left:0;top:150px;width:252px;height:52px;background:rgba(0,0,0,.55);color:var(--white);font-size:9px;font-weight:500;line-height:13px;padding:7px 10px}

/* features */
.features{left:75px;top:1026px;width:699px;height:96px;background:var(--panel)}
.feature-icon{width:58px;height:58px;border-radius:50%;background:var(--cyan);display:flex;align-items:center;justify-content:center}
.feature h3{font-size:12px;font-weight:400;color:var(--cyan)}
.feature p{font-size:9px;line-height:13.5px;color:#333;margin-top:3px;width:120px}

/* footer */
.site-footer{left:0;top:1130px;width:848px;height:70px;background:var(--navy);color:var(--white)}
.connect{left:77px;top:16px;font-size:8.5px;font-weight:500}
.social{left:77px;top:34px;display:flex;gap:10px}
.social span{width:13px;height:13px;border-radius:50%;background:var(--white)}
.footer-nav{right:73px;top:16px;font-size:7.5px;text-align:right;line-height:16px;text-transform:uppercase}
</style>
</head>
<body>

<header class="abs site-header">
  <div class="abs brand"><span class="brand-dot"></span>FERNWICK STUDY HUB</div>
</header>

<nav class="abs main-nav">
  <a href="#" style="width:118px;padding-left:56px">Home</a>
  <a href="#" style="width:103px;padding-left:20px">Who are we</a>
  <a href="#" style="width:93px;padding-left:20px">FSH News</a>
  <a href="#" style="width:131px;padding-left:23px">Learning system</a>
  <a href="#" style="width:110px;padding-left:23px">Testimonials</a>
  <a href="#" style="width:120px;padding-left:22px">Contact us</a>
</nav>

<section class="abs hero">
  <div class="abs hero-frame"></div>
  <div class="abs hero-slide" role="img" aria-label="Smiling young woman with glasses reading on a tablet in a bright office"></div>
  <p class="abs hero-caption">Lorem ipsum is simply<br>dummy text of<br>the printing</p>
  <a class="abs slide-arrow" style="left:79px" aria-label="Previous slide"><svg width="10" height="14" viewBox="0 0 10 14"><path d="M8 1 2 7l6 6" fill="none" stroke="#fff" stroke-width="2.5"/></svg></a>
  <a class="abs slide-arrow" style="left:735px" aria-label="Next slide"><svg width="10" height="14" viewBox="0 0 10 14"><path d="M2 1l6 6-6 6" fill="none" stroke="#fff" stroke-width="2.5"/></svg></a>
</section>

<section class="abs intro">
  <h1 class="abs intro-title">New interactive learning system</h1>
  <p class="abs intro-text">Contrary to popular belief, Lorem Ipsum is not simply random text. It has roots in a piece of classical Latin literature from 45 BC, making it over 2000 years old. Edwin Marlowe, a Latin professor at Harrowgate College in Virginia, looked up one of the more obscure Latin words, consectetur.</p>
</section>

<div class="abs bubble-shadow" style="left:238px;top:728px;width:70px"></div>
<div class="abs bubble-shadow" style="left:370px;top:752px;width:110px"></div>
<div class="abs bubble-shadow" style="left:543px;top:728px;width:70px"></div>
<div class="abs bubble" style="left:198px;top:575px;width:150px;height:150px">Assistente<br>Concierge</div>
<div class="abs bubble" style="left:503px;top:575px;width:150px;height:150px">The Best<br>Relationships<br>start off as<br>friendship</div>
<svg class="abs" style="left:314px;top:540px" width="220" height="220" viewBox="0 0 220 220" aria-hidden="true">
  <circle cx="110" cy="110" r="108" fill="none" stroke="#555" stroke-width="1" stroke-dasharray="3 3"/>
</svg>
<div class="abs bubble" style="left:330px;top:556px;width:188px;height:188px;background:radial-gradient(circle at 50% 60%,#c93a3a 0%,#e8e4df 35%,#bdbdbd 60%)" role="img" aria-label="Smiling boy with glasses holding letter blocks"></div>

<div class="abs rule" style="top:778px"></div>

<div class="abs news-panel"></div>
<h2 class="abs news-heading"><b>FSH</b>News</h2>

<div class="abs news-item" style="left:90px;top:828px"><span class="chev"><svg width="7" height="8" viewBox="0 0 7 8"><path d="M2 1l3 3-3 3" fill="none" stroke="#fff" stroke-width="1.6"/></svg></span><div><h3>Lorem Ipsum is simply</h3><p>looked up one of the more<br>obscure Latin words, consectetur.</p></div></div>
<div class="abs news-item" style="left:90px;top:883px"><span class="chev"><svg width="7" height="8" viewBox="0 0 7 8"><path d="M2 1l3 3-3 3" fill="none" stroke="#fff" stroke-width="1.6"/></svg></span><div><h3>There are many</h3><p>There are many variations of passages<br>of Lorem Ipsum available, but the.</p></div></div>
<div class="abs news-item" style="left:90px;top:942px"><span class="chev"><svg width="7" height="8" viewBox="0 0 7 8"><path d="M2 1l3 3-3 3" fill="none" stroke="#fff" stroke-width="1.6"/></svg></span><div><h3>Lorem Ipsum is simply dummy</h3><p>looked up one of the more<br>obscure Latin words, consectetur.</p></div></div>
<div class="abs news-item" style="left:318px;top:828px"><span class="chev"><svg width="7" height="8" viewBox="0 0 7 8"><path d="M2 1l3 3-3 3" fill="none" stroke="#fff" stroke-width="1.6"/></svg></span><div><h3>First true generator on</h3><p>The standard chunk of Lorem<br>Ipsum used since the 1500s is</p></div></div>
<div class="abs news-item" style="left:318px;top:883px"><span class="chev"><svg width="7" height="8" viewBox="0 0 7 8"><path d="M2 1l3 3-3 3" fill="none" stroke="#fff" stroke-width="1.6"/></svg></span><div><h3>Sed ut perspiciatis unde omn</h3><p>At vero eos et accusamus et iusto<br>odio dignissimos ducimus qui</p></div></div>
<div class="abs news-item" style="left:318px;top:942px"><span class="chev"><svg width="7" height="8" viewBox="0 0 7 8"><path d="M2 1l3 3-3 3" fill="none" stroke="#fff" stroke-width="1.6"/></svg></span><div><h3>But I must explain to you</h3><p>To take a trivial example, which of<br>us ever undertakes laborious</p></div></div>

<article class="abs about-card">
  <h2>Who <b>are</b> we?</h2>
  <div class="abs about-photo" role="img" aria-label="Group of five smiling business people in an office"></div>
  <p class="abs about-caption">On the other hand, we denounce with righteous indignation and dislike men who are so beguiled and demoralized by the charms.</p>
</article>

<div class="abs rule" style="top:1020px"></div>

<section class="abs features"></section>
<div class="abs feature-icon" style="left:93px;top:1037px"><svg width="16" height="18" viewBox="0 0 16 18"><circle cx="8" cy="5" r="4" fill="#fff"/><path d="M1 17c0-5 3-7 7-7s7 2 7 7z" fill="#fff"/></svg></div>
<div class="abs feature" style="left:165px;top:1038px"><h3>Be a friend instructor</h3><p>looked up one of the more obscure Latin words, consectetur.</p></div>
<div class="abs feature-icon" style="left:337px;top:1037px"><svg width="14" height="18" viewBox="0 0 14 18"><path d="M7 1a6 6 0 0 0-6 6c0 4 6 10 6 10s6-6 6-10a6 6 0 0 0-6-6z" fill="#fff"/><circle cx="7" cy="7" r="2.3" fill="var(--cyan)"/></svg></div>
<div class="abs feature" style="left:409px;top:1038px"><h3>Location</h3><p>looked up one of the more obscure Latin words, consectetur.</p></div>
<div class="abs feature-icon" style="left:580px;top:1037px"><svg width="18" height="14" viewBox="0 0 18 14"><path d="M1 14V8c0-4 2-7 6-8v3C5 4 4 5 4 7h3v7zM11 14V8c0-4 2-7 6-8v3c-2 1-3 2-3 4h3v7z" fill="#fff"/></svg></div>
<div class="abs feature" style="left:652px;top:1038px"><h3>Testimonials</h3><p>looked up one of the more obscure Latin words, consectetur.</p></div>

<footer class="abs site-footer">
  <p class="abs connect">CONNECT WITH US</p>
  <div class="abs social" aria-label="Social links"><span></span><span></span><span></span></div>
  <p class="abs footer-nav">Home &nbsp;\&nbsp; Who we are &nbsp;\&nbsp; FSH News &nbsp;\&nbsp; Testimonial &nbsp;/&nbsp; Contact us<br>Copyrights @ 2014 all rights reserved</p>
</footer>

</body>
</html>
```